Business card for law firm

Need business card for new law firm. Think confident, authoritative, conservative, but not stuffy or old-fashioned.

Contact Information for Business Card

Content for card - logo (uploaded), plus the following:

Paul Whitcombe (larger font)
Managing Partner (larger font, but not as large as name)
Level 9, 7 Ferris Lane
Sydney NSW 2000
Main Tel 02 9364 2710
Direct Tel 02 8472 3159
Email paul@qvlegal.com.au
www.qvlegal.com.au

Letterhead design should include logo plus:
Level 9, 7 Ferris Lane
Sydney NSW 2000
Tel 02 8472 3159
www.qvlegal.com.au

```html
<!DOCTYPE html>
<html lang="en">
<head>
<meta charset="utf-8">
<title>Quinvale Lawyers – Business Card</title>
<link rel="stylesheet" href="https://fonts.googleapis.com/css2?family=Cinzel:wght@500&family=Montserrat:wght@400&display=swap">
<style>
  :root {
    --backdrop: #1b1b1d;
    --navy: #262d6b;
    --navy-light: #2f3779;
    --ink: #ffffff;
    --ink-soft: rgba(255,255,255,0.92);
  }
  * { box-sizing: border-box; margin: 0; padding: 0; }
  html, body { width: 1200px; height: 900px; overflow: hidden; }
  body {
    background: var(--backdrop);
    font-family: "Montserrat", sans-serif;
    color: var(--ink);
    position: relative;
  }
  .card {
    position: absolute;
    left: 250px;
    width: 700px;
    height: 400px;
    background: var(--navy);
    overflow: hidden;
  }
  .card--back { top: 40px; }
  .card--front { top: 470px; }

  .back-pattern {
    position: absolute;
    inset: 0;
    background: linear-gradient(120deg, var(--navy) 0%, var(--navy-light) 55%, #3a4288 100%);
  }
  .back-mark {
    position: absolute;
    left: 50%; top: 50%;
    transform: translate(-50%, -50%);
    display: flex; align-items: center; gap: 10px;
    font-family: "Cinzel", serif;
    font-weight: 500;
    font-size: 18px;
    letter-spacing: 2px;
    color: var(--ink);
  }
  .mark-square { width: 14px; height: 14px; background: var(--ink); display: block; }

  .brand {
    position: absolute;
    right: 50px; top: 120px;
    display: flex; align-items: center; gap: 12px;
    font-family: "Cinzel", serif;
    font-weight: 500;
    font-size: 30px;
    letter-spacing: 1px;
    color: var(--ink);
  }
  .brand .mark-square { width: 22px; height: 22px; }

  .person {
    position: absolute;
    left: 50px; top: 180px;
  }
  .person__name {
    font-family: "Cinzel", serif;
    font-weight: 500;
    font-size: 24px;
    letter-spacing: 0.5px;
  }
  .person__role {
    font-size: 17px;
    color: var(--ink-soft);
    margin-top: 2px;
  }
  .website {
    position: absolute;
    right: 50px; top: 215px;
    font-size: 17px;
    letter-spacing: 2px;
  }
  .rule {
    position: absolute;
    left: 50px; right: 50px; top: 252px;
    height: 1.5px;
    background: var(--ink);
  }
  .contacts {
    position: absolute;
    left: 50px; top: 272px;
    list-style: none;
    font-size: 17px;
    line-height: 27px;
    letter-spacing: 0.5px;
  }
  .contacts li { display: flex; align-items: center; gap: 12px; }
  .contacts svg { width: 14px; height: 14px; flex: none; }
  .address {
    position: absolute;
    right: 50px; top: 285px;
    text-align: right;
    font-size: 19px;
    line-height: 30px;
    font-style: normal;
  }
</style>
</head>
<body>
  <section class="card card--back" aria-label="Card back">
    <div class="back-pattern" role="img" aria-label="Tonal embossed repeat pattern across the card"></div>
    <div class="back-mark"><span class="mark-square"></span>Quinvale</div>
  </section>

  <section class="card card--front" aria-label="Card front">
    <div class="brand"><span class="mark-square"></span>Quinvale Lawyers</div>

    <div class="person">
      <p class="person__name">PAUL WHITCOMBE</p>
      <p class="person__role">Managing Partner</p>
    </div>

    <p class="website">www.qvlegal.com.au</p>
    <div class="rule"></div>

    <ul class="contacts">
      <li>
        <svg viewBox="0 0 16 16" aria-hidden="true"><path d="M4 1.5l2.5 3-1.5 1.6c.8 1.9 2.3 3.4 4.2 4.2L10.8 8.8l3 2.5-1.3 2.7C7 13.6 2.4 9 2 3.4z" fill="none" stroke="#fff" stroke-width="1.3" stroke-linejoin="round"/></svg>
        02 9364 2710
      </li>
      <li>
        <svg viewBox="0 0 16 16" aria-hidden="true"><rect x="4" y="1" width="8" height="14" rx="1.5" fill="none" stroke="#fff" stroke-width="1.3"/><line x1="7" y1="12.5" x2="9" y2="12.5" stroke="#fff" stroke-width="1.3"/></svg>
        02 8472 3159
      </li>
      <li>
        <svg viewBox="0 0 16 16" aria-hidden="true"><rect x="1" y="3.5" width="14" height="9" fill="none" stroke="#fff" stroke-width="1.3"/><path d="M1 3.5l7 5 7-5" fill="none" stroke="#fff" stroke-width="1.3"/></svg>
        paul@qvlegal.com.au
      </li>
    </ul>

    <address class="address">
      Level 9, 7 Ferris Lane<br>
      Sydney NSW 2000
    </address>
  </section>
</body>
</html>
```